NexaBRIDGE new era @ Hyper Digitalization

We need a Brochure that show all our product, services and consulting related to Hyper Digitalization into the industrial internet of things world.
We need a document that can be handled as a electronic brochure, this means that we need to show strong corporate presence, with strong skill of technology, and we have credentials and key sucess projects related to Manufacturing industries.
Key industries that we attend: Automotive, Chemical, Food and Beverage, Mining, Paper and Pulp, Oil and Gas, Energy Management.
We save money to our customer in 6 ways: 1) Eficiency in operation 2) Production Control 3) Hyper Digitalization of Thing Optimizing asset ussage 4) Maintenance and predictive of assets risks 5) Quality Control reducing Cost 6) Augmented Reality in operation and control
Target Market(s)
Manufacturing Industry. CEO of companies that has challenges of saving operation costs into plants of manufacturing.
Industry/Entity Type
Software
Other font styles liked:
- MONTSERRAT
Requirements
Must have
- Technology Enviroment, our logo, our expertise, simple message about what our company does and the DNA, infography of the company, cases of sucess, cases of savings $ using our tecnology and services, what we can do for the customer in a few words
Nice to have
- standarize our colors related to our presentation, futuristic, information related to Artificial Inteligence related to machinery
Should not have
- old version of technology,

```html
<!DOCTYPE html>
<html lang="en">
<head>
<meta charset="utf-8">
<title>NexaBRIDGE Brochure 2021</title>
<link href="https://fonts.googleapis.com/css2?family=Montserrat:wght@400;500;600;700;800;900&display=swap" rel="stylesheet">
<style>
  :root{
    --page-bg:#f2f2f4;
    --navy-deep:#0d2438;
    --navy:#123e5e;
    --navy-mid:#16466a;
    --steel:#1c2f40;
    --sky:#9dbfcb;
    --brand-grey:#b9c2c9;
    --ink-dark:#133552;
    --white:#ffffff;
    --paper:#f5f8fb;
  }
  *{margin:0;padding:0;box-sizing:border-box}
  html,body{width:873px;height:1200px;overflow:hidden;background:var(--page-bg)}
  body{position:relative;font-family:"Montserrat",sans-serif;color:var(--white)}
  .spread{position:absolute;left:67px;width:739px;height:522px;overflow:hidden}
  .spread--cover{top:67px}
  .spread--inside{top:611px}
  .spread svg.art{position:absolute;inset:0;width:739px;height:522px}
  .wordmark{position:absolute;font-weight:600;font-size:22px;letter-spacing:.5px;color:var(--brand-grey);white-space:nowrap}
  .wordmark--back{left:87px;top:248px}
  .wordmark--front{left:404px;top:161px}
  .cover-title{position:absolute;left:404px;top:236px}
  .cover-title h1{font-weight:900;font-size:29px;letter-spacing:.3px;line-height:1}
  .cover-title p{font-weight:500;font-size:18px;margin-top:4px}
  .cover-url{position:absolute;right:23px;top:486px;font-size:10px;font-weight:700;color:var(--ink-dark)}
  .section-title{font-weight:800;font-size:24px;line-height:1}
  .themes{position:absolute;right:386px;top:67px;width:205px;text-align:right}
  .themes .section-title{margin-bottom:14px}
  .themes p{font-size:10px;line-height:11.9px;font-weight:400;margin-bottom:12px}
  .benefits{position:absolute;left:399px;top:67px;width:300px}
  .benefits .section-title{margin-bottom:16px}
  .benefit-list{list-style:none}
  .benefit-list li{position:relative;padding-left:17px;font-size:9.8px;line-height:11.9px;font-weight:500}
  .benefit-list svg{position:absolute;left:0;top:1px;width:11px;height:11px}
  .dna{position:absolute;left:399px;top:369px;width:285px}
  .dna .section-title{margin-bottom:9px}
  .dna p{font-size:7px;line-height:8.8px;font-weight:500}
  .dna h3{font-size:9.4px;font-weight:500;margin-top:12px;line-height:10px}
</style>
</head>
<body>

<section class="spread spread--cover">
  <svg class="art" viewBox="0 0 739 522">
    <defs>
      <linearGradient id="machine" x1="0" y1="0" x2="0" y2="1">
        <stop offset="0" stop-color="#1c3346"/><stop offset="1" stop-color="#0e2233"/>
      </linearGradient>
      <radialGradient id="earth" cx="0.85" cy="0.55" r="0.6">
        <stop offset="0" stop-color="#3f6f9a"/><stop offset=".55" stop-color="#142f52"/><stop offset="1" stop-color="#071426"/>
      </radialGradient>
      <linearGradient id="bottling" x1="0" y1="0" x2="1" y2="1">
        <stop offset="0" stop-color="#c9ccce"/><stop offset="1" stop-color="#6f767c"/>
      </linearGradient>
      <linearGradient id="businessman" x1="0" y1="0" x2="1" y2="1">
        <stop offset="0" stop-color="#8a8f94"/><stop offset="1" stop-color="#3b4148"/>
      </linearGradient>
    </defs>
    <rect x="0" y="0" width="369" height="522" fill="url(#machine)" role="img" aria-label="Dark blue-tinted photo of a bottling machine on a factory line"/>
    <rect x="369" y="0" width="370" height="522" fill="var(--navy)"/>
    <polygon points="459,0 739,0 739,270" fill="url(#earth)" role="img" aria-label="Earth from space with glowing network lines"/>
    <g stroke="#ffffff" stroke-width="1.4" opacity=".85">
      <line x1="545" y1="0" x2="710" y2="185"/>
      <line x1="580" y1="30" x2="739" y2="5"/>
    </g>
    <polygon points="487,522 739,522 739,271" fill="var(--paper)"/>
    <polygon points="640,245 739,343 640,442 541,343" fill="var(--navy-mid)"/>
    <polygon points="634,243 730,343 634,442 538,343" fill="url(#bottling)" stroke="#fff" stroke-width="2" role="img" aria-label="Photo of an industrial bottle filling carousel"/>
    <polygon points="550,367 620,438 550,510 479,438" fill="var(--navy-mid)"/>
    <polygon points="545,367 616,436 545,507 474,436" fill="url(#businessman)" stroke="#fff" stroke-width="2" role="img" aria-label="Photo of a smiling businessman using a phone"/>
  </svg>
  <div class="wordmark wordmark--back">NexaBRIDGE</div>
  <div class="wordmark wordmark--front">NexaBRIDGE</div>
  <div class="cover-title">
    <h1>BROCHURE</h1>
    <p>Nexabridge 2021</p>
  </div>
  <div class="cover-url">nexabridge-mx.com</div>
</section>

<section class="spread spread--inside">
  <svg class="art" viewBox="0 0 739 522">
    <defs>
      <linearGradient id="solar" x1="0" y1="0" x2="0.3" y2="1">
        <stop offset="0" stop-color="#a9b3ba"/>
        <stop offset=".18" stop-color="#7f8a8f"/>
        <stop offset=".3" stop-color="#5d6a66"/>
        <stop offset=".6" stop-color="#5a656c"/>
        <stop offset=".85" stop-color="#7a7868"/>
        <stop offset="1" stop-color="#9a917c"/>
      </linearGradient>
      <linearGradient id="mirror" x1="0" y1="0" x2="1" y2="1">
        <stop offset="0" stop-color="#a3aaae"/><stop offset=".45" stop-color="#9a9440"/><stop offset=".7" stop-color="#55606a"/><stop offset="1" stop-color="#2c3a48"/>
      </linearGradient>
      <linearGradient id="carline" x1="0" y1="0" x2="1" y2="0">
        <stop offset="0" stop-color="#6b6a55"/><stop offset=".6" stop-color="#3e4a52"/><stop offset="1" stop-color="#1e2327"/>
      </linearGradient>
    </defs>
    <rect x="0" y="0" width="369" height="522" fill="url(#solar)" role="img" aria-label="Photo of a solar concentrator tower over mirror fields in the mountains"/>
    <polygon points="125,0 369,0 369,522 166,522 73,116" fill="var(--steel)" opacity=".6"/>
    <polygon points="125,0 369,0 369,300 220,60" fill="var(--navy-deep)" opacity=".9"/>
    <polygon points="369,330 369,522 150,522" fill="var(--navy)" opacity=".9"/>
    <polygon points="237,272 358,395 237,519 116,395" fill="url(#mirror)" stroke="#fff" stroke-width="2" role="img" aria-label="Photo of a hexagonal mirror telescope assembly"/>
    <rect x="369" y="0" width="370" height="522" fill="var(--navy)"/>
    <g stroke="#6fa3b8" stroke-width=".6" opacity=".35" fill="none">
      <path d="M180 12 L160 120 M180 12 L205 120 M680 95 L640 210 M680 95 L705 210 M470 220 L520 120 L580 220"/>
    </g>
    <g fill="#5fb3a8" opacity=".6">
      <circle cx="180" cy="12" r="2"/><circle cx="680" cy="95" r="2"/><circle cx="520" cy="120" r="1.6"/>
    </g>
    <polygon points="608,0 739,0 739,47 677,93" fill="var(--sky)"/>
    <line x1="585" y1="0" x2="654" y2="90" stroke="#fff" stroke-width="1.4"/>
    <rect x="392" y="220" width="327" height="128" fill="url(#carline)" role="img" aria-label="Photo of car bodies on an automotive assembly line"/>
  </svg>

  <div class="themes">
    <h2 class="section-title">THEMES</h2>
    <p>We offer high performance technology</p>
    <p>State of the art in techniques with Artificial Intelligence and prototypes for new ways of doing manufacturing.</p>
    <p>We play the rol as an Architect for a Digital world into the shopfloor operation at Machine Levels</p>
  </div>

  <div class="benefits">
    <h2 class="section-title">Terms @ benefits</h2>
    <ul class="benefit-list">
      <li><svg viewBox="0 0 12 12"><circle cx="6" cy="6" r="5" fill="none" stroke="#fff" stroke-width="1"/><path d="M3.5 6l2 2 5-5.5" fill="none" stroke="#fff" stroke-width="1.1"/></svg>Reduce cost operation in manufacturing in 30%</li>
      <li><svg viewBox="0 0 12 12"><circle cx="6" cy="6" r="5" fill="none" stroke="#fff" stroke-width="1"/><path d="M3.5 6l2 2 5-5.5" fill="none" stroke="#fff" stroke-width="1.1"/></svg>Augmented Reality functions, adds 60% of productivity and efficiency at operator levels</li>
      <li><svg viewBox="0 0 12 12"><circle cx="6" cy="6" r="5" fill="none" stroke="#fff" stroke-width="1"/><path d="M3.5 6l2 2 5-5.5" fill="none" stroke="#fff" stroke-width="1.1"/></svg>Save 17% in Energy for production</li>
      <li><svg viewBox="0 0 12 12"><circle cx="6" cy="6" r="5" fill="none" stroke="#fff" stroke-width="1"/><path d="M3.5 6l2 2 5-5.5" fill="none" stroke="#fff" stroke-width="1.1"/></svg>Zero Unplanned Downtime in machine level</li>
      <li><svg viewBox="0 0 12 12"><circle cx="6" cy="6" r="5" fill="none" stroke="#fff" stroke-width="1"/><path d="M3.5 6l2 2 5-5.5" fill="none" stroke="#fff" stroke-width="1.1"/></svg>Optimize consistency in recipes by 10% delivers 32% of cost reduction</li>
      <li><svg viewBox="0 0 12 12"><circle cx="6" cy="6" r="5" fill="none" stroke="#fff" stroke-width="1"/><path d="M3.5 6l2 2 5-5.5" fill="none" stroke="#fff" stroke-width="1.1"/></svg>Supply Chain optimization by 1% of the cost of goods</li>
    </ul>
  </div>

  <div class="dna">
    <h2 class="section-title">Our DNA</h2>
    <p>We want all companies to operate in an automated way, to be more efficient and to compete with whoever is globally. We have the knowledge and experience to achieve it.</p>
    <h3>Our commitments:</h3>
    <p>Improve the operation of each company individullaly.<br>impacts the country's competitiveness<br>Support compaies to access the highest levels of development, productivity, inancing and profitability</p>
  </div>
</section>

</body>
</html>
```